Migration and redesign of existing website to WordPress using DIVI 3

I. TASK OBJECTIVE:
- Redesign our existing website www.kelvaleheelcare.com.au with a fresh new look and migrate to new Wordpress site based on DIVI3 theme. The site will contain the same basic functionality as the existing site (with some small changes).

II. STYLE/ DESIGN ASPECT:
As an example of a site that I like the look of, see https://pebblequarn.com/. I like the use of shadows, and this would go well with the little animations you can do with Divi (e.g. when hovering over pics).

1. What I am looking for is a design which has lots of white space, is modern and friendly looking (but still not too cute or frivolous, as we are a medical practice)
2. DESIGN that is NOT TOO rectangular or blocky.
3. Please take into consideration our Users are Older market, so any icons or navigation features need to be very easy to understand and not too small.
4. Must be easy to navigate
5. We are are happy to go with a new colour scheme, and are working on some ideas for this, but happy to take suggestions.

III. SPECIFICATIONS:
1. 5+ Pages (should flow like the current site)
2. Using Wordpress Divi 3 theme.
3. I'd like every page to have a "book now" button and a contact form in a sidebar so that users can click the button or fill in the contact form without scrolling at all. EXCEPT ON THE HOME PAGE, where there should still be a book now button (maybe on the top right in the header of all pages?), and maybe a contact us button which scrolls down to the contact area at the bottom of the HOME page. I don't think a side bar is necessarily required on the home page, but if you think it makes sense from a design perspective please let me know.
4. AT THE BOTTOM OF THE PAGE, just above the FOOTER, I'd like a row of trust logos for various organisations that we are affiliated with. (A list of this company will be provided later but you could temporarily use placeholders)

Once we have a structure in place, we can migrate most of the content. Please let me know if I'm not being clear or you need further information.

Podiatry Customers and Referrors

Health Care

5+ page

• Simple to navigate.
• Contact/booking details on most if not all pages - please see specification above
• Section for Trusted Affiliates above the footer
• Wordpress using Divi3 Theme
• Not too busy with the design. Plenty of white space or light background.
• Should not be complicated to navigate.
• TOO rectangular or blocky designs

```html
<!DOCTYPE html>
<html lang="en">
<head>
<meta charset="utf-8">
<title>Kelvale Heel &amp; Ankle Clinic</title>
<link rel="stylesheet" href="https://fonts.googleapis.com/css2?family=Lora:wght@400;700&family=Open+Sans:wght@400;600&display=swap">
<style>
:root{
  --teal:#0b6d86;
  --teal-dark:#08566b;
  --teal-light:#1a8aa6;
  --ink:#2b2b2b;
  --muted:#8a8f93;
  --line:#e3e6e8;
  --footer:#12343f;
  --footer-deep:#0c2630;
  --white:#ffffff;
  --photo-a:#c9d6db;
  --photo-b:#8fa9b3;
}
*{box-sizing:border-box;margin:0;padding:0}
html,body{width:1200px;height:2820px;overflow:hidden;background:var(--white)}
body{font-family:"Open Sans",Arial,sans-serif;color:var(--ink);font-size:13px}
h1,h2,h3,h4,.serif{font-family:"Lora",Georgia,serif}

/* Header */
.site-header{height:90px;position:relative;padding:0 100px}
.brand{position:absolute;left:100px;top:14px;display:flex;align-items:center;gap:10px}
.brand-mark{width:46px;height:46px;border-radius:50%;background:var(--teal)}
.brand-name{font-family:"Lora",Georgia,serif;font-size:16px;font-weight:700;color:var(--teal);line-height:1.15;width:150px}
.top-bar{position:absolute;right:100px;top:12px;display:flex;align-items:center;gap:10px}
.top-phone{font-size:12px;color:var(--teal);margin-right:14px;font-weight:600}
.social{width:22px;height:22px;background:var(--teal);border-radius:2px}
.main-nav{position:absolute;right:100px;top:58px;display:flex;gap:20px}
.main-nav a{font-family:"Lora",Georgia,serif;font-size:13px;color:var(--ink);text-decoration:none}

/* Hero */
.hero{position:relative;height:430px;background:linear-gradient(100deg,#3f5e69 0%,#7d9aa4 45%,#c3d0d4 75%,#9fb3ba 100%);padding:90px 100px 0}
.hero h1{color:var(--white);font-size:38px;font-weight:700;width:620px;line-height:1.2}
.hero p{color:var(--white);font-size:16px;line-height:1.55;width:500px;margin-top:12px}
.btn{display:inline-block;background:var(--teal);color:var(--white);font-family:"Lora",Georgia,serif;font-size:13px;padding:9px 18px;border-radius:2px}
.hero .btn{margin-top:26px;font-size:15px;padding:12px 22px}
.dots{position:absolute;left:50%;bottom:22px;transform:translateX(-50%);display:flex;gap:6px}
.dots span{width:8px;height:8px;border-radius:50%;background:rgba(255,255,255,.55)}
.dots span.on{background:var(--white)}

/* Main */
.content{height:2012px;padding:70px 100px 0;display:flex;gap:50px;position:relative}
.blog{width:600px}
.section-title{font-size:19px;font-weight:700;color:var(--ink);letter-spacing:.5px;margin-bottom:28px}
.post{display:flex;gap:28px;height:290px;margin-bottom:30px}
.post-photo{width:250px;height:260px;flex:none;background:linear-gradient(135deg,var(--photo-a),var(--photo-b))}
.post-body{padding-top:10px}
.post-title{font-size:16px;color:var(--teal);font-weight:700}
.post-meta{font-size:11px;color:var(--muted);margin:10px 0 14px}
.post-meta b{color:var(--teal);font-weight:600}
.post-excerpt{font-size:12px;color:var(--muted);line-height:1.75}
.post-actions{margin-top:18px;display:flex;gap:12px}
.post-actions .btn{font-size:12px;padding:7px 16px}
.load-more{text-align:center;font-family:"Lora",Georgia,serif;font-size:14px;font-weight:700;color:var(--teal);margin-top:4px}

.sidebar{width:350px}
.appointment{background:var(--teal);padding:0 0 26px;box-shadow:0 6px 16px rgba(0,0,0,.18)}
.appointment h3{background:var(--teal-dark);color:var(--white);font-size:16px;text-align:center;padding:14px 0;font-weight:400}
.field{margin:12px 28px 0;height:32px;border:1px solid rgba(255,255,255,.55);color:var(--white);font-size:12px;padding:7px 10px;position:relative}
.field.half{display:inline-block;width:136px;margin-right:0}
.field.message{height:92px}
.field svg{position:absolute;right:8px;top:8px}
.appointment .btn{display:block;width:110px;margin:18px auto 0;background:var(--white);color:var(--teal);text-align:center}
.side-title{text-align:center;font-size:18px;font-weight:700;margin:64px 0 22px}
.latest-item{display:flex;gap:14px;margin-bottom:18px}
.latest-photo{width:100px;height:66px;flex:none;background:linear-gradient(135deg,var(--photo-a),var(--photo-b))}
.latest-item .post-title{font-size:13px;line-height:1.35}
.latest-item .post-meta{margin:6px 0 0}
.popular-card{margin-bottom:26px}
.popular-photo{height:190px;background:linear-gradient(135deg,#d7e2e6,#93acb5)}
.popular-card h4{font-size:14px;margin-top:14px;letter-spacing:.5px}
.popular-card .post-meta{margin:6px 0 8px}
.sidebar .center{text-align:center}

/* Footer */
.site-footer{height:288px;background:var(--footer);color:#c9d6da;position:relative}
.footer-cols{display:flex;padding:40px 100px 0;gap:60px}
.footer-col h4{color:var(--white);font-size:14px;letter-spacing:.6px;margin-bottom:16px}
.footer-col p{font-size:11.5px;line-height:1.75}
.col-about{width:290px}
.col-contact{width:260px}
.col-news{width:290px}
.contact-line{display:flex;align-items:center;gap:8px;font-size:11.5px;margin-bottom:8px}
.subscribe{display:flex;margin-top:14px}
.subscribe span{flex:1;height:30px;border:1px solid rgba(255,255,255,.4);font-size:11px;padding:7px 10px}
.subscribe b{width:40px;height:30px;background:var(--teal-light)}
.footer-social{display:flex;gap:10px;margin-top:18px}
.footer-social span{width:24px;height:24px;background:var(--white);border-radius:2px}
.copyright{position:absolute;left:0;right:0;bottom:0;height:44px;background:var(--footer-deep);text-align:center;font-size:11px;line-height:44px;color:#a9bcc2}
</style>
</head>
<body>

<header class="site-header">
  <div class="brand">
    <span class="brand-mark"></span>
    <span class="brand-name">Kelvale Heel &amp; Ankle Clinic</span>
  </div>
  <div class="top-bar">
    <span class="top-phone">Call (08) 9123 4567</span>
    <span class="social"></span><span class="social"></span><span class="social"></span><span class="social"></span>
  </div>
  <nav class="main-nav">
    <a>Home</a><a>Common Problems</a><a>Services</a><a>About Us</a><a>Shop Online</a><a>Helpful Information</a><a>Blog</a><a>Contact</a><a>Previous</a>
  </nav>
</header>

<section class="hero" role="img" aria-label="Photo of a podiatrist examining a patient's foot">
  <h1>We Offer Solutions To Common Foot Problems</h1>
  <p>Lorem Ipsum is simply dummy text of the printing and typesetting industry. Lorem Ipsum has been the industry's standard dummy text ever since the 1500s.</p>
  <span class="btn">Book An Appointment</span>
  <div class="dots"><span class="on"></span><span></span><span></span></div>
</section>

<main class="content">
  <section class="blog">
    <h2 class="section-title">BLOG POSTS</h2>

    <article class="post">
      <div class="post-photo" role="img" aria-label="Photo of a foot being treated with a pink file"></div>
      <div class="post-body">
        <h3 class="post-title">Lorem Ipsum Is Simply Dummy Text</h3>
        <p class="post-meta"><b>Sample Me</b> &nbsp;|&nbsp; 12 October, 2017</p>
        <p class="post-excerpt">There are many variations of passages of lorem ipsum available, but the majority have suffered alteration in some form, by injected humour, or randomised words which don't look even slightly believable.</p>
        <div class="post-actions"><span class="btn">Read More</span><span class="btn">Share</span></div>
      </div>
    </article>

    <article class="post">
      <div class="post-photo" role="img" aria-label="Photo of hands massaging a foot"></div>
      <div class="post-body">
        <h3 class="post-title">Lorem Ipsum Is Simply Dummy Text</h3>
        <p class="post-meta"><b>Sample Me</b> &nbsp;|&nbsp; 12 October, 2017</p>
        <p class="post-excerpt">There are many variations of passages of lorem ipsum available, but the majority have suffered alteration in some form, by injected humour, or randomised words which don't look even slightly believable.</p>
        <div class="post-actions"><span class="btn">Read More</span><span class="btn">Share</span></div>
      </div>
    </article>

    <article class="post">
      <div class="post-photo" role="img" aria-label="Photo of a foot reflexology session"></div>
      <div class="post-body">
        <h3 class="post-title">Lorem Ipsum Is Simply Dummy Text</h3>
        <p class="post-meta"><b>Sample Me</b> &nbsp;|&nbsp; 12 October, 2017</p>
        <p class="post-excerpt">There are many variations of passages of lorem ipsum available, but the majority have suffered alteration in some form, by injected humour, or randomised words which don't look even slightly believable.</p>
        <div class="post-actions"><span class="btn">Read More</span><span class="btn">Share</span></div>
      </div>
    </article>

    <article class="post">
      <div class="post-photo" role="img" aria-label="Photo of a foot being examined with a cotton swab"></div>
      <div class="post-body">
        <h3 class="post-title">Lorem Ipsum Is Simply Dummy Text</h3>
        <p class="post-meta"><b>Sample Me</b> &nbsp;|&nbsp; 12 October, 2017</p>
        <p class="post-excerpt">There are many variations of passages of lorem ipsum available, but the majority have suffered alteration in some form, by injected humour, or randomised words which don't look even slightly believable.</p>
        <div class="post-actions"><span class="btn">Read More</span><span class="btn">Share</span></div>
      </div>
    </article>

    <article class="post">
      <div class="post-photo" role="img" aria-label="Photo of feet during a foot treatment"></div>
      <div class="post-body">
        <h3 class="post-title">Lorem Ipsum Is Simply Dummy Text</h3>
        <p class="post-meta"><b>Sample Me</b> &nbsp;|&nbsp; 12 October, 2017</p>
        <p class="post-excerpt">There are many variations of passages of lorem ipsum available, but the majority have suffered alteration in some form, by injected humour, or randomised words which don't look even slightly believable.</p>
        <div class="post-actions"><span class="btn">Read More</span><span class="btn">Share</span></div>
      </div>
    </article>

    <p class="load-more">LOAD MORE</p>
  </section>

  <aside class="sidebar">
    <div class="appointment">
      <h3>Appointment Form</h3>
      <div class="field">Name</div>
      <div class="field">Phone</div>
      <div class="field">Email</div>
      <div class="field">Date
        <svg width="14" height="14" viewBox="0 0 14 14"><rect x="1" y="2" width="12" height="11" fill="none" stroke="#fff"/><line x1="1" y1="5" x2="13" y2="5" stroke="#fff"/></svg>
      </div>
      <div class="field">Time
        <svg width="14" height="14" viewBox="0 0 14 14"><circle cx="7" cy="7" r="6" fill="none" stroke="#fff"/><path d="M7 3v4h3" fill="none" stroke="#fff"/></svg>
      </div>
      <div class="field message">Message</div>
      <span class="btn">Book Now</span>
    </div>

    <h3 class="side-title">LATEST POSTS</h3>
    <div class="latest-item">
      <div class="latest-photo" role="img" aria-label="Photo of a foot massage"></div>
      <div><p class="post-title serif">Lorem Ipsum Is Simply Dummy Text</p><p class="post-meta"><b>Sample Me</b> | 12 Oct, 2017</p></div>
    </div>
    <div class="latest-item">
      <div class="latest-photo" role="img" aria-label="Photo of a foot care treatment"></div>
      <div><p class="post-title serif">Lorem Ipsum Is Simply Dummy Text</p><p class="post-meta"><b>Sample Me</b> | 12 Oct, 2017</p></div>
    </div>
    <div class="latest-item">
      <div class="latest-photo" role="img" aria-label="Photo of a heel examination"></div>
      <div><p class="post-title serif">Lorem Ipsum Is Simply Dummy Text</p><p class="post-meta"><b>Sample Me</b> | 12 Oct, 2017</p></div>
    </div>
    <div class="latest-item">
      <div class="latest-photo" role="img" aria-label="Photo of a pedicure treatment"></div>
      <div><p class="post-title serif">Lorem Ipsum Is Simply Dummy Text</p><p class="post-meta"><b>Sample Me</b> | 12 Oct, 2017</p></div>
    </div>

    <h3 class="side-title">MOST POPULAR POSTS</h3>
    <div class="popular-card">
      <div class="popular-photo" role="img" aria-label="Photo of a patient receiving a foot massage"></div>
      <h4>LOREM IPSUM TEXT</h4>
      <p class="post-meta">12 October, 2017</p>
      <p class="post-excerpt">Lorem ipsum dolor sit amet, consectetur adipisicing elit, sed do eiusmod tempor incididunt ut labore et dolore magna.</p>
    </div>
    <div class="popular-card">
      <div class="popular-photo" role="img" aria-label="Photo of a therapist treating a patient's leg"></div>
      <h4>LOREM IPSUM TEXT</h4>
      <p class="post-meta">12 October, 2017</p>
      <p class="post-excerpt">Lorem ipsum dolor sit amet, consectetur adipisicing elit, sed do eiusmod tempor incididunt ut labore et dolore magna.</p>
    </div>
    <p class="center"><span class="btn">See More</span></p>
  </aside>
</main>

<footer class="site-footer">
  <div class="footer-cols">
    <div class="footer-col col-about">
      <h4 class="serif">ABOUT</h4>
      <p>Sed ut perspiciatis unde omnis iste natus error sit voluptatem accusantium doloremque laudantium, totam rem aperiam, eaque ipsa quae ab illo inventore veritatis.</p>
    </div>
    <div class="footer-col col-contact">
      <h4 class="serif">CONTACT</h4>
      <div class="contact-line">
        <svg width="12" height="14" viewBox="0 0 12 14"><path d="M6 13S1 8 1 5a5 5 0 0 1 10 0c0 3-5 8-5 8z" fill="#c9d6da"/><circle cx="6" cy="5" r="1.8" fill="#12343f"/></svg>
        27 Sample Street, Kelvale WA 6000
      </div>
      <div class="contact-line">
        <svg width="12" height="12" viewBox="0 0 12 12"><path d="M2 1l2.5 0 1 3-1.5 1a7 7 0 0 0 3 3l1-1.5 3 1V10a1 1 0 0 1-1 1A10 10 0 0 1 1 2a1 1 0 0 1 1-1z" fill="#c9d6da"/></svg>
        (08) 9123 4567
      </div>
      <div class="contact-line">
        <svg width="13" height="10" viewBox="0 0 13 10"><rect x=".5" y=".5" width="12" height="9" fill="none" stroke="#c9d6da"/><path d="M.5.5l6 5 6-5" fill="none" stroke="#c9d6da"/></svg>
        info@kelvaleheelcare.com.au
      </div>
    </div>
    <div class="footer-col col-news">
      <h4 class="serif">SUBSCRIBE TO NEWSLETTER</h4>
      <p>Subscribe to receive our latest foot care tips and clinic news straight to your inbox.</p>
      <div class="subscribe"><span>Your Email Address</span><b></b></div>
      <div class="footer-social"><span></span><span></span><span></span><span></span></div>
    </div>
  </div>
  <p class="copyright">© 2017 Kelvale Heel &amp; Ankle Clinic. All Rights Reserved.</p>
</footer>

</body>
</html>
```